Web Design Project

Psychotherapy and Counselling Practice needs a landing page web design.

My business "Larkfield Advisory" specialises in the treatment of Anxiety and Depression with a holistic approach, endeavouring to unlock the key that holds us to ransom in a life that is imbalanced, frustrating, and ultimately of our own making due to our own perceptions and behaviours.

There is much that impacts us which we cannot change, but we are always in control of how we think, and how we frame our experiences.....learning to challenge those thoughts and behaviours that are destructive and disempowering opens up a world of joyful possibility. Life is about making choices, learn to make wiser and healthier choices.......

Larkfield Advisory has a client base of individual clients but will seek to expand to offer services to the Corporate world by offering an adjunct to employers for established "Wellness Programs".

Larkfield Advisory is a highly professional, ethically bound business, with the needs of the client at the forefront of all we do.

Larkfield Advisory wishes to avoid the usual "jargon driven" psychobabble offered on many counselling web pages. It aims to be stylishly presented, clean in look and with as few "words" as possible and a largely white background (faster loading and more powerful impact of what is stated), those words contained in the webpage should be meaningful, persuasive and have an impact simply at glance. Larkfield does not want , or expect, those prospective clients in need of support , to be reading through volumes of industry driven cliches.

At this point Larkfield is just looking for a high quality landing page. However in time this will likely expand to include other sections such as case studies, video content etc.

Target Market(s)

Those in need of emotional support, suffering mental health issues, and those simply wanting to become self aware supported by a mindful therapist.

Industry/Entity Type

Industry

Requirements
Must have
• The design must incorporate the Larkfield logo and colour schemes found on the attached files.

```html
<!DOCTYPE html>
<html lang="en">
<head>
<meta charset="utf-8">
<title>Larkfield Advisory</title>
<link rel="stylesheet" href="https://fonts.googleapis.com/css2?family=PT+Sans:wght@400;700&display=swap">
<style>
  :root {
    --leaf: #8aa913;
    --leaf-light: #b9d14a;
    --stone: #8d8d8d;
    --stone-dark: #6f6f6f;
    --mist: #f4f4f4;
    --paper: #ffffff;
  }
  * { margin: 0; padding: 0; box-sizing: border-box; }
  html, body { width: 1200px; height: 891px; overflow: hidden; background: var(--paper); }
  body { font-family: "PT Sans", sans-serif; color: var(--stone); }
  .page { position: relative; width: 1200px; height: 891px; background: linear-gradient(180deg, #fff 0%, #f7f7f7 40%, #fff 80%); }

  .brand { position: absolute; left: 84px; top: 62px; display: flex; align-items: center; gap: 14px; }
  .brand-dot { width: 56px; height: 56px; border-radius: 50%; background: var(--leaf); }
  .brand-name { font-size: 26px; font-weight: 700; color: var(--leaf); }

  .main-nav { position: absolute; top: 82px; right: 72px; display: flex; gap: 30px; }
  .main-nav a { font-size: 18px; font-weight: 700; color: var(--leaf); text-decoration: none; letter-spacing: .3px; }

  .hero-panel { position: absolute; left: 612px; top: 222px; width: 546px; height: 470px; background: var(--paper); opacity: .85; }

  .vine { position: absolute; left: 270px; top: 226px; width: 64px; height: 510px;
    background: linear-gradient(180deg, rgba(138,169,19,.15), rgba(138,169,19,.55)); border-radius: 32px; }
  .wordmark { position: absolute; left: 80px; top: 446px; font-size: 84px; font-weight: 400; color: var(--leaf); letter-spacing: 3px; line-height: 1; }

  .quote { position: absolute; left: 727px; top: 264px; font-size: 28px; font-weight: 700; color: var(--stone); line-height: 44px; }
  .quote span { display: block; padding-left: 16px; }
  .quote-author { position: absolute; left: 741px; top: 358px; font-size: 16px; font-weight: 700; color: var(--stone); }

  .tagline { position: absolute; left: 741px; top: 477px; font-size: 22px; font-weight: 700; color: var(--stone); }
  .tagline em { font-style: normal; color: var(--leaf); }

  .practitioner { position: absolute; left: 741px; top: 545px; }
  .practitioner h2 { font-size: 22px; font-weight: 700; color: var(--stone); }
  .practitioner .credentials { font-size: 16px; font-weight: 700; margin-top: 6px; }
  .practitioner .contact { font-size: 17px; font-weight: 700; margin-top: 26px; line-height: 26px; }

  .ground { position: absolute; left: 0; top: 690px; }

  .site-footer { position: absolute; left: 0; top: 812px; width: 1200px; height: 79px; background: var(--paper); }
  .copyright { position: absolute; left: 83px; top: 38px; font-size: 12px; font-weight: 700; color: var(--stone-dark); }
  .social { position: absolute; left: 432px; top: 23px; display: flex; gap: 10px; }
  .social span { width: 30px; height: 29px; background: var(--leaf); display: block; }
  .web-address { position: absolute; right: 72px; top: 34px; font-size: 17px; font-weight: 700; color: var(--stone-dark); }
  .web-address em { font-style: normal; color: var(--leaf); }
</style>
</head>
<body>
<div class="page">
  <header>
    <div class="brand"><span class="brand-dot"></span><span class="brand-name">Larkfield Advisory</span></div>
    <nav class="main-nav">
      <a href="#">HOME</a><a href="#">ABOUT US</a><a href="#">CASE STUDIES</a><a href="#">VIDEO CONTENT</a>
    </nav>
  </header>

  <div class="hero-panel"></div>
  <div class="vine" role="img" aria-label="Climbing green vine illustration"></div>
  <div class="wordmark">LARKFIELD</div>

  <blockquote class="quote">“With the new day comes<span>new strength new thoughts.”</span></blockquote>
  <p class="quote-author">( Helen Marlowe )</p>

  <p class="tagline"><em>Advisory</em> is highly Professional</p>

  <section class="practitioner">
    <h2>MARA ELLISON</h2>
    <p class="credentials">BA (Psych) BSc (Hons) Psych MBPS</p>
    <p class="contact">Mobile: 0400 555 218<br>E-mail: mara.ellison@mailhub.net</p>
  </section>

  <svg class="ground" width="1200" height="122" viewBox="0 690 1200 122" aria-hidden="true">
    <defs>
      <linearGradient id="band" x1="0" y1="0" x2="0" y2="1">
        <stop offset="0" stop-color="#8a8a8a"/><stop offset="1" stop-color="#6c6c6c"/>
      </linearGradient>
    </defs>
    <path d="M0 748 C300 740 700 722 1200 738 L1200 812 L0 812 Z" fill="url(#band)"/>
    <path d="M0 705 C260 742 700 726 1090 711 C720 734 300 748 0 738 Z" fill="#8aa913"/>
  </svg>

  <footer class="site-footer">
    <p class="copyright">© Copyright Larkfield 2013 . Alright reserve</p>
    <div class="social"><span></span><span></span></div>
    <p class="web-address">www.<em>larkfieldadvisory</em>.com.au</p>
  </footer>
</div>
</body>
</html>
```